Social Media Graphics - Oakline Push REVISED

Create 6-7 individual social media graphics (square size) to encourage folks to join our online course called:

The Harvest Ledger Circle
How to Launch a Multi-Million Business From Scratch
Sign Up Today!

IMPORTANT: Make the largest and most prominent text on the graphic be: How to Launch a Multi-Million Business From Scratch

For the color scheme of the graphics, let's try a blue color palette; make sure the graphics appeal to both men and women

Make sure each graphic contains 1 of the 3 pics attached (crop pic as needed); and make sure one of the graphics is all TEXT only.

Target Market(s)

men and women looking to start a business

Industry/Entity Type

Entrepreneurship

Colors
0054AA
0677BA
7BADD7
CADEEF
E8F1F8

Requirements
Must have
• All the text and use the 3 pics provided; one graphic can be all text; Simple, modern design that's easy to read

```html
<!DOCTYPE html>
<html lang="en">
<head>
<meta charset="utf-8">
<title>The Harvest Ledger Circle – Social Graphics</title>
<link href="https://fonts.googleapis.com/css2?family=Bebas+Neue&family=Oswald:wght@500;700&family=Poppins:wght@300;400;600;700;800&family=Anton&display=swap" rel="stylesheet">
<style>
  :root {
    --blue-deep: #0054aa;
    --blue-mid: #0677ba;
    --blue-soft: #7badd7;
    --blue-pale: #cadeef;
    --blue-mist: #e8f1f8;
    --cyan: #18c4e6;
    --navy: #1b2235;
    --white: #ffffff;
  }
  * { margin: 0; padding: 0; box-sizing: border-box; }
  html, body { width: 1200px; height: 846px; overflow: hidden; background: var(--white); }
  p { white-space: nowrap; }
  .board { position: relative; width: 1200px; height: 846px; }
  .tile { position: absolute; width: 346px; height: 346px; overflow: hidden; }
  .tile--a { left: 45px;  top: 55px; }
  .tile--b { left: 424px; top: 55px; }
  .tile--c { left: 806px; top: 55px; }
  .tile--d { left: 45px;  top: 441px; }
  .tile--e { left: 424px; top: 441px; }
  .tile--f { left: 806px; top: 441px; }

  .abs { position: absolute; }
  .center-x { left: 0; right: 0; text-align: center; }
  .bebas { font-family: "Bebas Neue", "Oswald", sans-serif; line-height: 1; }
  .poppins { font-family: "Poppins", sans-serif; line-height: 1; }
  .anton { font-family: "Anton", "Bebas Neue", sans-serif; line-height: 1; }
  .photo { position: absolute; }

  /* Tile A */
  .tile--a { background: linear-gradient(180deg, #2aa6e4 0%, var(--blue-mid) 45%, var(--blue-deep) 100%); color: var(--white); }
  .tile--a .brand { top: 11px; font-size: 15px; font-weight: 300; letter-spacing: .3px; }
  .tile--a .photo { left: 80px; top: 32px; width: 190px; height: 210px; background: radial-gradient(ellipse at 50% 40%, #274a75 0%, #1b3557 60%, rgba(6,119,186,0) 100%); }
  .tile--a .lead { top: 194px; font-size: 56px; letter-spacing: -.5px; }
  .tile--a .sub { top: 243px; font-size: 33px; letter-spacing: -.4px; }
  .tile--a .band { left: 0; right: 0; top: 281px; height: 35px; background: var(--navy); }
  .tile--a .scratch { top: 283px; font-size: 33px; font-weight: 800; }
  .tile--a .cta { top: 323px; font-size: 14px; font-weight: 600; }

  /* Tile B */
  .tile--b { background: radial-gradient(ellipse at 55% 40%, var(--white) 0%, var(--blue-mist) 50%, var(--blue-pale) 100%); }
  .tile--b .frame { left: 17px; right: 17px; top: 24px; bottom: 30px; border: 1.3px dashed var(--blue-mid); }
  .tile--b .tab { left: 84px; width: 178px; top: 0; height: 41px; background: var(--blue-mid); border-radius: 0 0 18px 18px; }
  .tile--b .tab-text { top: 11px; font-size: 19px; color: var(--white); }
  .tile--b .lead { top: 62px; font-size: 44px; color: var(--navy); letter-spacing: -.5px; }
  .tile--b .mid { top: 110px; font-size: 58px; color: var(--blue-mid); letter-spacing: -1px; }
  .tile--b .big { top: 160px; font-size: 82px; color: var(--blue-mid); letter-spacing: -1px; }
  .tile--b .rule { left: 42px; right: 42px; height: 1px; background: var(--blue-soft); }
  .tile--b .scratch { top: 244px; font-family: "Oswald", sans-serif; font-weight: 700; font-size: 33px; color: var(--navy); letter-spacing: 1px; line-height: 1; }
  .tile--b .pill { left: 81px; width: 184px; top: 302px; height: 30px; border-radius: 15px; background: linear-gradient(90deg, var(--blue-mid), var(--blue-deep)); }
  .tile--b .cta { top: 308px; font-size: 17px; font-weight: 800; color: var(--white); }

  /* Tile C */
  .tile--c { background: linear-gradient(160deg, var(--blue-mid) 0%, var(--blue-deep) 55%, var(--cyan) 100%); color: var(--white); }
  .tile--c .brand { top: 14px; font-size: 10px; letter-spacing: 5px; font-weight: 600; }
  .tile--c .pill { left: 29px; width: 288px; top: 34px; height: 30px; border-radius: 15px; background: var(--navy); }
  .tile--c .pill-text { top: 38px; font-size: 23px; font-weight: 800; }
  .tile--c .mid { top: 66px; font-size: 56px; letter-spacing: -.5px; }
  .tile--c .big { top: 108px; font-size: 100px; letter-spacing: -1px; left: 24px; }
  .tile--c .band { left: 0; width: 205px; top: 199px; height: 97px; background: linear-gradient(90deg, var(--navy), #203a78); }
  .tile--c .from { left: 24px; top: 205px; font-family: "Poppins", sans-serif; font-weight: 800; font-size: 40px; line-height: 1; }
  .tile--c .scratch { left: 24px; top: 246px; font-size: 46px; }
  .tile--c .cta { left: 22px; top: 307px; font-family: "Oswald", sans-serif; font-weight: 700; font-size: 17px; letter-spacing: 1px; line-height: 1; }
  .tile--c .photo { left: 160px; top: 175px; width: 186px; height: 171px; background: linear-gradient(180deg, #1c2a40 0%, #2b2f3d 50%, #d8345a 100%); border-radius: 60px 60px 0 0; }

  /* Tile D */
  .tile--d { background: var(--white); border: 1px solid var(--blue-pale); }
  .tile--d .topbar { left: 0; width: 180px; top: 0; height: 21px; background: linear-gradient(90deg, #1a3fa0, #2757d6); }
  .tile--d .brand { left: 0; width: 180px; top: 28px; text-align: center; font-size: 16px; color: var(--blue-mid); letter-spacing: .3px; }
  .tile--d .photo { left: 0; width: 185px; top: 49px; height: 297px; background: linear-gradient(180deg, #2454c8 0%, #17307a 40%, #0e1a38 100%); }
  .tile--d .col { left: 185px; width: 161px; text-align: center; }
  .tile--d .l1 { top: 17px; font-size: 50px; color: var(--navy); }
  .tile--d .l2 { top: 64px; font-size: 42px; color: var(--navy); }
  .tile--d .l3 { top: 108px; font-size: 64px; color: var(--blue-mid); }
  .tile--d .l4 { top: 167px; font-size: 48px; color: var(--blue-mid); }
  .tile--d .l5 { top: 211px; font-size: 40px; color: var(--blue-mid); }
  .tile--d .l6 { top: 259px; font-size: 32px; color: var(--navy); letter-spacing: -.3px; }
  .tile--d .band { left: 185px; right: 0; top: 297px; height: 34px; background: var(--navy); }
  .tile--d .cta { top: 307px; font-size: 12px; font-weight: 600; letter-spacing: 1.5px; color: var(--white); }

  /* Tile E */
  .tile--e { background: radial-gradient(ellipse at 50% 35%, var(--white) 0%, var(--blue-mist) 55%, var(--blue-pale) 100%); }
  .tile--e .brand { top: 24px; font-size: 10px; letter-spacing: 4px; color: var(--navy); }
  .tile--e .lead { top: 57px; font-size: 25px; font-weight: 800; color: var(--navy); letter-spacing: -.3px; }
  .tile--e .band { left: 0; right: 0; top: 240px; bottom: 0; background: linear-gradient(180deg, var(--blue-mid), var(--blue-deep)); }
  .tile--e .huge { top: 90px; font-size: 92px; letter-spacing: 2px; background: linear-gradient(90deg, var(--blue-soft), var(--blue-deep)); -webkit-background-clip: text; background-clip: text; color: transparent; }
  .tile--e .million { top: 176px; font-size: 70px; color: var(--blue-deep); letter-spacing: 1px; }
  .tile--e .sub { top: 257px; font-size: 35px; color: var(--white); letter-spacing: -.3px; }
  .tile--e .pill { left: 94px; width: 158px; top: 303px; height: 26px; border-radius: 13px; background: var(--navy); }
  .tile--e .cta { top: 308px; font-size: 15px; font-weight: 800; color: var(--white); }

  /* Tile F */
  .tile--f { background: linear-gradient(180deg, var(--blue-mid) 0%, #0a8fd0 60%, var(--cyan) 100%); color: var(--white); }
  .tile--f .tab { left: 78px; width: 190px; top: 0; height: 26px; background: var(--white); border-radius: 0 0 12px 12px; }
  .tile--f .tab-text { top: 7px; font-size: 14px; letter-spacing: 1px; color: var(--navy); }
  .tile--f .lead { top: 31px; font-size: 52px; letter-spacing: -.5px; }
  .tile--f .sub { top: 84px; font-size: 31px; letter-spacing: -.4px; }
  .tile--f .scratch { top: 114px; font-size: 54px; letter-spacing: -.5px; }
  .tile--f .photo { left: 65px; top: 172px; width: 240px; height: 140px; background: radial-gradient(ellipse at 50% 60%, #1d3050 0%, #1a3a66 55%, rgba(6,119,186,0) 100%); }
  .tile--f .band { left: 0; right: 0; top: 312px; bottom: 0; background: var(--navy); border-top: 2px solid var(--cyan); }
  .tile--f .cta { top: 320px; font-size: 15px; font-weight: 600; }
</style>
</head>
<body>
<main class="board">

  <section class="tile tile--a">
    <p class="abs center-x poppins brand">THE HARVEST LEDGER CIRCLE</p>
    <div class="photo" role="img" aria-label="Photo of the two course hosts standing together, arms crossed"></div>
    <p class="abs center-x bebas lead">HOW TO LAUNCH</p>
    <p class="abs center-x bebas sub">A MULTI-MILLION BUSINESS</p>
    <div class="abs band"></div>
    <p class="abs center-x poppins scratch">FROM SCRATCH</p>
    <p class="abs center-x poppins cta">SIGN UP TODAY!</p>
  </section>

  <section class="tile tile--b">
    <div class="abs frame"></div>
    <div class="abs tab"></div>
    <p class="abs center-x bebas tab-text">THE HARVEST LEDGER CIRCLE</p>
    <p class="abs center-x bebas lead">HOW TO LAUNCH A</p>
    <div class="abs rule" style="top:106px"></div>
    <p class="abs center-x bebas mid">MULTI-MILLION</p>
    <p class="abs center-x bebas big">BUSINESS</p>
    <div class="abs rule" style="top:238px"></div>
    <p class="abs center-x scratch">FROM SCRATCH</p>
    <div class="abs pill"></div>
    <p class="abs center-x poppins cta">SIGN UP TODAY!</p>
  </section>

  <section class="tile tile--c">
    <p class="abs center-x poppins brand">THE HARVEST LEDGER CIRCLE</p>
    <div class="abs pill"></div>
    <p class="abs center-x poppins pill-text">HOW TO LAUNCH</p>
    <p class="abs center-x bebas mid">A MULTI-MILLION</p>
    <p class="abs bebas big">BUSINESS</p>
    <div class="abs band"></div>
    <p class="abs from">FROM</p>
    <p class="abs bebas scratch">SCRATCH</p>
    <p class="abs cta">SIGN UP TODAY!</p>
    <div class="photo" role="img" aria-label="Photo of the two course hosts smiling, arms crossed"></div>
  </section>

  <section class="tile tile--d">
    <div class="abs topbar"></div>
    <p class="abs bebas brand">THE HARVEST LEDGER CIRCLE</p>
    <div class="photo" role="img" aria-label="Photo of the two hosts on stage, one speaking into a microphone"></div>
    <p class="abs col bebas l1">HOW TO</p>
    <p class="abs col bebas l2">LAUNCH A</p>
    <p class="abs col bebas l3">MULTI</p>
    <p class="abs col bebas l4">MILLION</p>
    <p class="abs col bebas l5">BUSINESS</p>
    <p class="abs col bebas l6">FROM SCRATCH</p>
    <div class="abs band"></div>
    <p class="abs col poppins cta">SIGN UP TODAY!</p>
  </section>

  <section class="tile tile--e">
    <p class="abs center-x poppins brand">THE HARVEST LEDGER CIRCLE</p>
    <p class="abs center-x poppins lead">HOW TO LAUNCH A</p>
    <div class="abs band"></div>
    <p class="abs center-x anton huge">MULTI</p>
    <p class="abs center-x anton million">MILLION</p>
    <p class="abs center-x bebas sub">BUSINESS FROM SCRATCH</p>
    <div class="abs pill"></div>
    <p class="abs center-x poppins cta">SIGN UP TODAY!</p>
  </section>

  <section class="tile tile--f">
    <div class="abs tab"></div>
    <p class="abs center-x bebas tab-text">THE HARVEST LEDGER CIRCLE</p>
    <p class="abs center-x bebas lead">HOW TO LAUNCH</p>
    <p class="abs center-x bebas sub">A MULTI-MILLION BUSINESS</p>
    <p class="abs center-x bebas scratch">FROM SCRATCH</p>
    <div class="photo" role="img" aria-label="Photo of the two course hosts standing together, arms crossed"></div>
    <div class="abs band"></div>
    <p class="abs center-x poppins cta">SIGN UP TODAY!</p>
  </section>

</main>
</body>
</html>
```